Custom Cabinet Shop Needs a website design

Hi,
We need a website for a Custom Cabinet Shop and Cabinet parts manufacturing business.
The business has two sides to it. One side provides custom Kitchens, vanities, entertainment units, offices and what not to homeowners and contractors.
The 2nd side of the business provides built to order cabinet boxes and other parts required to put together a project to other cabinet shops, small contractors looking to install there own cabinets.
Website will need a Gallery to display work.
Color scheme to go well with logo.
current website is www.brambleoakcustomcabinets.com
being changed to www.brambleoak.ca
Logo Included in attached files.
Tagline "Joinery with Spirit"
Mission Statement "Our passion is to deliver inspired cabinetry solutions to suit all your needs, supported by our phenomenal star class customer service"
The website should convey quality and professionalism.
Thank you.
Homeowners/ Contractors
Entertainment

```html
<!DOCTYPE html>
<html lang="en">
<head>
<meta charset="utf-8">
<title>Bramble Oak Custom Cabinets</title>
<link href="https://fonts.googleapis.com/css2?family=Open+Sans:wght@400;600;700&display=swap" rel="stylesheet">
<style>
  :root {
    --orange: #f05a22;
    --orange-deep: #d9481a;
    --ink: #222222;
    --topbar: #3b3b3b;
    --nav-text: #9a9a9a;
    --nav-active: #c9c9c9;
    --paper: #ffffff;
    --muted: #777777;
    --header-top: #ffffff;
    --header-bottom: #e6e6e6;
  }
  * { box-sizing: border-box; margin: 0; padding: 0; }
  html, body { width: 1200px; height: 858px; overflow: hidden; background: var(--paper); }
  body { font-family: "Open Sans", Arial, sans-serif; color: var(--ink); }

  .topbar { height: 30px; background: var(--topbar); display: flex; align-items: center; justify-content: space-between; padding: 0 60px; }
  .social { display: flex; gap: 12px; }
  .social-dot { width: 12px; height: 12px; border-radius: 50%; background: #bdbdbd; }
  .search { width: 190px; height: 18px; border: 1px solid #cfcfcf; border-radius: 9px; background: #f4f4f4; display: flex; align-items: center; justify-content: space-between; padding: 0 8px; font-size: 9px; color: #888; }

  .site-header { height: 80px; background: linear-gradient(var(--header-top), var(--header-bottom)); display: flex; justify-content: space-between; padding-left: 60px; border-bottom: 3px solid var(--orange); }
  .brand { display: flex; align-items: center; gap: 10px; }
  .brand-mark { width: 28px; height: 28px; border-radius: 50%; background: var(--orange); }
  .brand-name { font-size: 26px; font-weight: 700; color: var(--ink); letter-spacing: 0.5px; }
  .main-nav { display: flex; padding-right: 60px; }
  .main-nav a { display: flex; align-items: center; padding: 0 18px; font-size: 14px; color: var(--nav-text); text-decoration: none; }
  .main-nav a.active { background: var(--nav-active); color: var(--paper); font-weight: 600; }

  .hero { position: relative; height: 327px; background: linear-gradient(160deg, #2e3440 0%, #4a3a2c 45%, #7a5a3a 70%, #3a2e26 100%); color: var(--paper); text-align: center; }
  .hero-copy { position: absolute; top: 110px; left: 0; right: 0; }
  .hero-title { font-size: 26px; font-weight: 400; line-height: 1.25; letter-spacing: 0.5px; }
  .hero-sub { font-size: 13px; margin-top: 8px; }
  .slide-arrow { position: absolute; top: 150px; width: 26px; height: 26px; background: var(--orange); display: flex; align-items: center; justify-content: center; }
  .slide-arrow.prev { left: 0; } .slide-arrow.next { right: 0; }
  .slide-dots { position: absolute; bottom: 14px; left: 0; right: 0; display: flex; justify-content: center; gap: 6px; }
  .slide-dots span { width: 9px; height: 9px; border-radius: 50%; background: rgba(255,255,255,0.55); }

  .welcome { height: 210px; background: linear-gradient(var(--orange), var(--orange-deep)); color: var(--paper); display: flex; gap: 40px; padding: 20px 60px; }
  .welcome-left { width: 380px; }
  .welcome-kicker { font-size: 14px; text-transform: uppercase; }
  .welcome-title { font-size: 22px; font-weight: 700; line-height: 1.1; }
  .welcome-photo { margin-top: 10px; height: 115px; background: linear-gradient(120deg, #5a4a40, #b9a28c 60%, #e8ddd0); border: 3px solid var(--paper); }
  .about { flex: 1; }
  .about-title { font-size: 22px; font-weight: 700; }
  .about-sub { font-size: 10px; font-weight: 600; text-transform: uppercase; margin-bottom: 8px; }
  .about-text { font-size: 12px; line-height: 1.55; max-width: 640px; }
  .read-more { display: inline-block; margin-top: 12px; background: var(--paper); color: var(--orange); font-size: 10px; font-weight: 700; padding: 5px 12px; text-transform: uppercase; }

  .services { display: flex; gap: 40px; padding: 14px 60px 0; }
  .service { flex: 1; }
  .service-head { display: flex; align-items: center; gap: 8px; font-size: 12px; font-weight: 700; height: 26px; }
  .service-icon { width: 14px; height: 14px; background: var(--orange); }
  .service-photo { height: 82px; margin-top: 6px; }
  .photo-kitchen { background: linear-gradient(120deg, #3a3a3a, #8a8a8a); }
  .photo-furniture { background: linear-gradient(120deg, #f2f2f2, #c9c2b8 60%, #9a7b5c); }
  .photo-consult { background: linear-gradient(120deg, #cfd8dc, #c0392b 55%, #e8e0d8); }
  .service-text { font-size: 11px; color: var(--muted); line-height: 1.45; margin-top: 7px; }
  .more-link { display: inline-flex; align-items: center; gap: 5px; margin-top: 6px; font-size: 10px; color: var(--orange); }
  .more-link::after { content: ""; width: 10px; height: 10px; border-radius: 50%; background: #cfcfcf; }
</style>
</head>
<body>
  <div class="topbar">
    <div class="social" aria-label="Social links">
      <span class="social-dot"></span><span class="social-dot"></span><span class="social-dot"></span><span class="social-dot"></span><span class="social-dot"></span>
    </div>
    <div class="search">Search
      <svg width="9" height="9" viewBox="0 0 10 10"><circle cx="4" cy="4" r="3" fill="none" stroke="#888" stroke-width="1.3"/><line x1="6.3" y1="6.3" x2="9" y2="9" stroke="#888" stroke-width="1.3"/></svg>
    </div>
  </div>

  <header class="site-header">
    <div class="brand"><span class="brand-mark"></span><span class="brand-name">BRAMBLE OAK</span></div>
    <nav class="main-nav">
      <a class="active" href="#">Home</a><a href="#">Gallery</a><a href="#">Services</a><a href="#">Warranty</a><a href="#">Contact</a>
    </nav>
  </header>

  <section class="hero" role="img" aria-label="Photo of a custom kitchen with dark cabinets, live-edge island and bar stools">
    <div class="hero-copy">
      <h1 class="hero-title">OUR BEST SERVICES<br>FOR BEST CLIENTS</h1>
      <p class="hero-sub">Emergent eradicate, medical supplies assistance, education pride challenges of our times.</p>
    </div>
    <span class="slide-arrow prev"><svg width="10" height="10" viewBox="0 0 10 10"><polyline points="7,1 3,5 7,9" fill="none" stroke="#fff" stroke-width="1.6"/></svg></span>
    <span class="slide-arrow next"><svg width="10" height="10" viewBox="0 0 10 10"><polyline points="3,1 7,5 3,9" fill="none" stroke="#fff" stroke-width="1.6"/></svg></span>
    <div class="slide-dots"><span></span><span></span><span></span></div>
  </section>

  <section class="welcome">
    <div class="welcome-left">
      <p class="welcome-kicker">Welcome to</p>
      <h2 class="welcome-title">Bramble Oak Custom Cabinets</h2>
      <div class="welcome-photo" role="img" aria-label="Photo of a finished living room with built-in fireplace cabinetry"></div>
    </div>
    <div class="about">
      <h2 class="about-title">ABOUT</h2>
      <p class="about-sub">Crafted cabinetry since day one</p>
      <p class="about-text">We design and build custom kitchens, vanities, entertainment units and offices for homeowners and contractors, and supply built to order cabinet boxes and parts to other shops. Every piece is measured, cut and finished in our own shop with care.</p>
      <span class="read-more">Read more</span>
    </div>
  </section>

  <section class="services">
    <article class="service">
      <div class="service-head"><span class="service-icon"></span>Kitchen &amp; Bath Design</div>
      <div class="service-photo photo-kitchen" role="img" aria-label="Photo of a modern kitchen"></div>
      <p class="service-text">Full kitchen and bath layouts planned around how you cook, store and live every day.</p>
      <span class="more-link">more</span>
    </article>
    <article class="service">
      <div class="service-head"><span class="service-icon"></span>New &amp; Existing Furniture Arrangements</div>
      <div class="service-photo photo-furniture" role="img" aria-label="Photo of a bright white kitchen with wood floor"></div>
      <p class="service-text">Fresh arrangements for new pieces and existing furniture to make each room work better.</p>
      <span class="more-link">more</span>
    </article>
    <article class="service">
      <div class="service-head"><span class="service-icon"></span>Interior Structural Consulting</div>
      <div class="service-photo photo-consult" role="img" aria-label="Photo of a red lounge chair in a sunlit room"></div>
      <p class="service-text">Practical advice on interior structure, walls and openings before any cabinet goes in.</p>
      <span class="more-link">more</span>
    </article>
  </section>
</body>
</html>
```